body therapist

I need to offer my services as a massage therapist at home, acclimating customer space aroma candles with music and everything else to bring comfort. 8 offer rituals like this: relaxing ritual, purifying ritual, ritual breast, facial and body cleansing ritual organic, ritual man, ritual feet, slimming ritual. Naraja handling colors, seawater, green, lavender

Target Market(s)

men and women, tired, stressed, looking for something new

Font styles to use
Decorative
Script

Colors
f37122
0493ce
abd037

Requirements
Must have
• detailing each massage
Nice to have
• simple and elegant

```html
<!DOCTYPE html>
<html lang="es">
<head>
<meta charset="utf-8">
<title>Cuerpo Sereno – Masajes a domicilio</title>
<link href="https://fonts.googleapis.com/css2?family=Italianno&family=Lora:ital,wght@0,400;0,700;1,400;1,700&display=swap" rel="stylesheet">
<style>
  :root {
    --ink: #2e1d1b;
    --blush: #ecdedb;
    --rule: #d8c0bb;
    --paper: #ffffff;
    --skin-light: #f3e6df;
    --skin-mid: #d9a98a;
    --mat: #e4d3b8;
    --naranja: #f37122;
    --agua: #0493ce;
    --verde: #abd037;
  }
  * { margin: 0; padding: 0; box-sizing: border-box; }
  html, body { width: 1200px; height: 927px; overflow: hidden; background: var(--paper); }
  .brochure { position: relative; width: 1200px; height: 927px; color: var(--ink); font-family: "Lora", serif; }
  .script { font-family: "Italianno", cursive; font-weight: 400; }

  .panel { position: absolute; background: var(--blush); }
  .panel--top { left: 78px; top: 0; width: 436px; height: 254px; }
  .panel--bottom { left: 78px; top: 672px; width: 436px; height: 255px; }
  .panel__title { position: absolute; left: 38px; top: 36px; font-size: 43px; line-height: 1; white-space: nowrap; }
  .panel__intro { position: absolute; left: 39px; top: 103px; width: 354px; font-size: 16.5px; line-height: 22px; text-align: justify; }

  .rituals { position: absolute; left: 39px; top: 176px; width: 360px; list-style: none;
    display: grid; grid-template-columns: 1fr 1fr; column-gap: 12px; row-gap: 3px; font-size: 11.5px; line-height: 15px; }
  .rituals li { display: flex; align-items: baseline; gap: 5px; white-space: nowrap; }
  .rituals li::before { content: ""; flex: none; width: 7px; height: 7px; border-radius: 50%; background: var(--dot); transform: translateY(-1px); }
  .rituals b { font-weight: 700; }
  .rituals .c-naranja { --dot: var(--naranja); }
  .rituals .c-agua { --dot: var(--agua); }
  .rituals .c-verde { --dot: var(--verde); }

  .rule { position: absolute; left: 0; width: 600px; height: 6px; background: var(--rule); }
  .rule--top { top: 254px; }
  .rule--bottom { top: 666px; }

  .photo { position: absolute; }
  .photo--left { left: 0; top: 260px; width: 600px; height: 406px;
    background: linear-gradient(180deg, #fbf8f6 0%, var(--skin-light) 35%, var(--skin-mid) 55%, #f6f1ee 80%, #ffffff 100%); }
  .photo--right { left: 600px; top: 470px; width: 600px; height: 378px;
    background: linear-gradient(180deg, #fbf7f4 0%, var(--skin-light) 30%, var(--skin-mid) 55%, var(--mat) 85%, #eef0f2 100%); }

  .contact { position: absolute; display: flex; align-items: center; gap: 8px; font-style: italic; font-weight: 700; font-size: 29px; line-height: 1; white-space: nowrap; }
  .contact svg { width: 20px; height: 22px; fill: var(--agua); }
  .contact--left { left: 112px; top: 541px; }
  .contact--right { left: 788px; top: 871px; }
  .hours { position: absolute; left: 130px; top: 588px; width: 200px; text-align: center; font-style: italic; font-weight: 700; font-size: 19px; line-height: 25px; }

  .prices { position: absolute; left: 39px; top: 18px; width: 357px; }
  .prices__heading { font-weight: 700; font-size: 24px; line-height: 30px; }
  .prices__row { display: flex; justify-content: space-between; font-size: 26px; line-height: 32.5px; }
  .panel__tagline { position: absolute; left: 0; width: 436px; top: 166px; text-align: center; font-size: 42px; line-height: 1.1; }

  .brand { position: absolute; left: 700px; top: 92px; width: 440px; display: flex; align-items: center; justify-content: center; gap: 16px; }
  .brand__mark { width: 22px; height: 22px; border-radius: 50%; background: var(--naranja); }
  .brand__name { font-family: "Italianno", cursive; font-size: 82px; line-height: 1; }

  .intro-right { position: absolute; left: 620px; top: 322px; width: 560px; text-align: center; font-size: 32px; line-height: 40px; }
</style>
</head>
<body>
<main class="brochure">
  <section class="panel panel--top">
    <h1 class="panel__title script">Terapeuta de masajes a domicilio</h1>
    <p class="panel__intro">La tarifa de precios se aplica por tiempo de servicio, independientemente del tipo de masaje solicitado</p>
    <ul class="rituals">
      <li class="c-naranja"><b>Relajante</b> alivia estrés y tensión</li>
      <li class="c-agua"><b>Purificante</b> libera toxinas</li>
      <li class="c-verde"><b>Pecho</b> suave y reafirmante</li>
      <li class="c-naranja"><b>Limpieza orgánica</b> rostro y cuerpo</li>
      <li class="c-agua"><b>Hombre</b> espalda y músculos</li>
      <li class="c-verde"><b>Pies</b> reflexología ligera</li>
      <li class="c-naranja"><b>Reductor</b> modela la figura</li>
    </ul>
  </section>

  <div class="rule rule--top"></div>
  <div class="photo photo--left" role="img" aria-label="Foto de un hombre relajado recibiendo un masaje en la espalda sobre una camilla blanca"></div>
  <div class="rule rule--bottom"></div>

  <p class="contact contact--left">
    <svg viewBox="0 0 24 24" aria-hidden="true"><path d="M6.6 10.8a15.1 15.1 0 0 0 6.6 6.6l2.2-2.2c.3-.3.7-.4 1-.2 1.1.4 2.3.6 3.6.6.6 0 1 .4 1 1V20c0 .6-.4 1-1 1A17 17 0 0 1 3 4c0-.6.4-1 1-1h3.5c.6 0 1 .4 1 1 0 1.3.2 2.5.6 3.6.1.3 0 .7-.2 1z"/></svg>
    1 800-555-0147
  </p>
  <p class="hours">Lunes a Sabado<br>8 a 21 hrs.</p>

  <section class="panel panel--bottom">
    <div class="prices">
      <h2 class="prices__heading">Precios:</h2>
      <div class="prices__row"><span>30 Minutos</span><span>20 €</span></div>
      <div class="prices__row"><span>60 Minutos</span><span>40 €</span></div>
      <div class="prices__row"><span>90 Minutos</span><span>60 €</span></div>
    </div>
    <p class="panel__tagline script">Disfruta de un masaje relajante</p>
  </section>

  <div class="brand">
    <span class="brand__mark"></span>
    <span class="brand__name">Cuerpo Sereno</span>
  </div>

  <p class="intro-right script">Terapeuta de masajes a domicilio<br>ambientando el espacio del cliente con música, aromas velas<br>y todo lo demas para brindar bienestar y mejor salud.</p>

  <div class="photo photo--right" role="img" aria-label="Foto de una mujer con una flor en el cabello recibiendo un masaje en los hombros"></div>

  <p class="contact contact--right">
    <svg viewBox="0 0 24 24" aria-hidden="true"><path d="M6.6 10.8a15.1 15.1 0 0 0 6.6 6.6l2.2-2.2c.3-.3.7-.4 1-.2 1.1.4 2.3.6 3.6.6.6 0 1 .4 1 1V20c0 .6-.4 1-1 1A17 17 0 0 1 3 4c0-.6.4-1 1-1h3.5c.6 0 1 .4 1 1 0 1.3.2 2.5.6 3.6.1.3 0 .7-.2 1z"/></svg>
    1 800-555-0147
  </p>
</main>
</body>
</html>
```